I need a flyer made , the flyer can be one page or two pages or three pages . I will be posting this on Instagram and social media platforms. I am a luxury home builder , I am looking to hire a construction project manager . Below are some examples and ideas what can be on the flyer

We’re looking for a construction project manager who’s passionate about building luxury homes at the highest standards
We’re hiring construction project manager
* Experience 5+ years in residential project management with a strong portfolio of completed homes.
* location : Bergen County NJ
* excellent leadership skills, leads teams with confidence and clarity
* communicates seamlessly with architects , engineers, designers and clients
*knows how to manage budgets and timelines without compromising quality
*solves problems with a positive solution first mindset
* pays attention to every detail because in luxury the small things are the big things

Apply now , link in bio or DM to connect.

My logo is attached, my web site www.velstridebuilders.com
My style is modern but still warm and inviting. I like a clean classy look .

Please don’t add any images of chairs or people to the flyer , I do not want people on my flyer. Do not add standard images of offices and houses , we are luxury builders , we build homes over 2 million dollars. Keep a classy , simple modern look . High end .

You can add a white hard hat with my logo on it for a image , this is a suggestion does not have to be on my flyer ,

```html
<!DOCTYPE html>
<html lang="en">
<head>
<meta charset="UTF-8">
<title>Velstride Builders – We're Hiring</title>
<link href="https://fonts.googleapis.com/css2?family=Anton&family=Poppins:wght@400;500;600;700;800&display=swap" rel="stylesheet">
<style>
  :root{
    --gold:#cf9f55;
    --ink:#111111;
    --navy:#0e121c;
    --panel:#e1e1e1;
    --white:#ffffff;
    --muted:#1d1d1d;
  }
  *{margin:0;padding:0;box-sizing:border-box}
  html,body{width:1200px;height:1200px;overflow:hidden;background:var(--white)}
  .flyer{position:relative;width:1200px;height:1200px;overflow:hidden;font-family:"Poppins",sans-serif;color:var(--ink);background:var(--white)}
  .left-panel{position:absolute;left:0;top:0;width:621px;height:1050px;background:var(--panel)}
  .footer-band{position:absolute;left:0;top:1050px;width:621px;height:150px;background:var(--navy);display:flex;align-items:center;justify-content:center}
  .footer-band .url{color:var(--white);font-size:33px;font-weight:500;letter-spacing:.3px}
  .architecture-photo{position:absolute;left:621px;top:0;width:579px;height:253px;background:linear-gradient(180deg,#f6f6f6 0%,#cfcfcf 60%,#9a9a9a 100%)}
  .wordmark{position:absolute;left:30px;top:100px;width:560px;text-align:center;font-family:"Poppins",sans-serif;font-weight:600;font-size:50px;line-height:1;color:var(--ink)}
  .hero-panel{position:absolute;left:63px;top:253px;width:1104px;height:447px;border-radius:26px;background:linear-gradient(180deg,#2b2b2b 0%,#0d0d0d 55%,#000 100%)}
  .manager-photo{position:absolute;left:700px;top:157px;width:467px;height:543px;border-radius:140px 26px 26px 0;background:linear-gradient(160deg,#f3f3f3 0%,#cfd9e8 35%,#f08a3c 70%,#b0b7c2 100%)}
  .megaphone-art{position:absolute;left:0;top:492px;width:138px;height:178px;border-radius:20px;background:radial-gradient(circle at 45% 55%,#e7e2d7 0%,#cfb07a 50%,rgba(207,159,85,0) 72%)}
  .badge-were{position:absolute;left:154px;top:287px;width:221px;height:72px;background:var(--white);border-radius:8px;display:flex;align-items:center;justify-content:center;font-weight:800;font-size:62px;letter-spacing:-2px;color:var(--ink);z-index:2}
  .badge-were::after{content:"";position:absolute;left:118px;bottom:-12px;border-left:10px solid transparent;border-right:10px solid transparent;border-top:12px solid var(--white)}
  .headline{position:absolute;left:152px;top:346px;font-family:"Anton",sans-serif;font-size:212px;line-height:1;color:var(--gold);letter-spacing:0}
  .role{position:absolute;left:150px;top:570px;color:var(--white);font-weight:800;font-size:45px;line-height:1.05}
  .slogan{position:absolute;left:0;top:722px;width:621px;text-align:center;font-size:32px;color:var(--ink)}
  .slogan b{font-weight:700}
  .location-pill{position:absolute;left:124px;top:776px;width:413px;height:55px;background:var(--gold);border-radius:12px;display:flex;align-items:center;padding-left:20px;gap:16px;font-weight:700;font-size:33px;color:var(--ink)}
  .apply-button{position:absolute;left:186px;top:848px;width:291px;height:78px;background:var(--ink);border-radius:10px;display:flex;align-items:center;justify-content:center;gap:12px;color:var(--white);font-weight:700;font-size:31px;box-shadow:0 4px 0 #000}
  .cta-note{position:absolute;left:0;top:942px;width:621px;text-align:center;color:var(--gold);font-weight:700;font-size:25px;letter-spacing:-.2px}
  .handle{position:absolute;left:0;top:980px;width:621px;display:flex;justify-content:center;align-items:center;gap:14px}
  .handle .dot{width:30px;height:30px;border-radius:50%;background:var(--gold)}
  .handle .text{font-size:29px;letter-spacing:2.5px;color:var(--ink)}
  .requirements{position:absolute;left:670px;top:740px;width:470px}
  .requirements h2{font-weight:700;font-size:34px;line-height:1.1;color:var(--muted)}
  .requirements .lead{font-size:19.5px;line-height:1.2;margin-top:6px;color:var(--muted)}
  .requirements hr{border:0;height:1px;background:linear-gradient(90deg,#999,rgba(153,153,153,0));margin:14px 0 14px}
  .checklist{list-style:none}
  .checklist li{position:relative;padding-left:35px;font-size:17.5px;line-height:1.22;margin-bottom:12px;color:#222}
  .checklist li b{font-weight:600}
  .checklist svg{position:absolute;left:0;top:8px}
</style>
</head>
<body>
<div class="flyer">
  <div class="left-panel"></div>
  <div class="architecture-photo" role="img" aria-label="Black and white modern luxury home with architectural wireframe overlay"></div>

  <div class="wordmark">Velstride Builders</div>

  <div class="hero-panel"></div>
  <div class="manager-photo" role="img" aria-label="Construction project manager in hard hat and safety vest holding a clipboard"></div>
  <div class="megaphone-art" role="img" aria-label="Gold megaphone illustration"></div>

  <div class="badge-were">WE’RE</div>
  <div class="headline">HIRING</div>
  <div class="role">CONSTRUCTION<br>PROJECT MANAGER</div>

  <p class="slogan"><b>Build</b> Luxury. <b>Lead</b> Excellence.</p>

  <div class="location-pill">
    <svg width="24" height="32" viewBox="0 0 24 32" aria-hidden="true"><path d="M12 1C6 1 1.5 5.5 1.5 11.3 1.5 19 12 31 12 31s10.5-12 10.5-19.7C22.5 5.5 18 1 12 1z" fill="#fff"/><circle cx="12" cy="11.5" r="4" fill="#cf9f55"/></svg>
    <span>Bergen County, NJ</span>
  </div>

  <div class="apply-button">
    <span>APPLY NOW</span>
    <svg width="46" height="46" viewBox="0 0 46 46" aria-hidden="true"><g stroke="#fff" stroke-width="2.5" stroke-linecap="round"><line x1="16" y1="4" x2="16" y2="11"/><line x1="6" y1="9" x2="11" y2="14"/><line x1="3" y1="19" x2="10" y2="19"/><line x1="26" y1="8" x2="22" y2="13"/></g><path d="M16 17 L40 27 L30 30 L37 40 L32 43 L25 33 L18 40 Z" fill="#fff"/></svg>
  </div>

  <p class="cta-note">LINK IN BIO OR DM TO CONNECT.</p>
  <div class="handle"><span class="dot"></span><span class="text">velstridebuilders</span></div>

  <div class="footer-band"><span class="url">www.velstridebuilders.com</span></div>

  <section class="requirements">
    <h2>EXPERIENCE 5+ YEARS</h2>
    <p class="lead">in residential project management with a strong portfolio of completed homes.</p>
    <hr>
    <ul class="checklist">
      <li><svg width="22" height="22" viewBox="0 0 22 22" aria-hidden="true"><circle cx="11" cy="11" r="9.5" fill="none" stroke="#cf9f55" stroke-width="1.5"/><path d="M6.5 11.2l3 3 6-6.2" fill="none" stroke="#cf9f55" stroke-width="1.6"/></svg><b>Excellent leadership skills,</b> leads teams<br>with confidence and clarity</li>
      <li><svg width="22" height="22" viewBox="0 0 22 22" aria-hidden="true"><circle cx="11" cy="11" r="9.5" fill="none" stroke="#cf9f55" stroke-width="1.5"/><path d="M6.5 11.2l3 3 6-6.2" fill="none" stroke="#cf9f55" stroke-width="1.6"/></svg><b>Communicates seamlessly</b> with architects ,<br>engineers, designers and clients</li>
      <li><b>Knows how to manage budgets and timelines</b><br>without compromising quality</li>
      <li><svg width="22" height="22" viewBox="0 0 22 22" aria-hidden="true"><circle cx="11" cy="11" r="9.5" fill="none" stroke="#cf9f55" stroke-width="1.5"/><path d="M6.5 11.2l3 3 6-6.2" fill="none" stroke="#cf9f55" stroke-width="1.6"/></svg><b>Solves problems</b> with a positive solution<br>first mindset</li>
      <li><svg width="22" height="22" viewBox="0 0 22 22" aria-hidden="true"><circle cx="11" cy="11" r="9.5" fill="none" stroke="#cf9f55" stroke-width="1.5"/><path d="M6.5 11.2l3 3 6-6.2" fill="none" stroke="#cf9f55" stroke-width="1.6"/></svg><b>Pays attention to every detail</b> because in<br>luxury the small things are the big things</li>
    </ul>
  </section>
</div>
</body>
</html>
```